13 Varno - new website design project

Our company Varno Electrical is developing a new lead generation website focused on Electrical, LED Lighting and Solar Power. We need a high converting website.

Example of our current website is www.varnoelectrical-example.com.au You can take content from this website for this new design. Our colours are red, black and white. For our new website we would like to promote Varno, Spark Every Day. Please listen to the jingle.

The below link is the company jingle that we have developed.
http://www.tunecraftdemo.com.au/vrn-tc-v1/

The key for this brief is to generate leads for Electrical, LED Lighting (for commercial) and Solar Power & Storage.

Target Market(s)

Business owners in Melbourne Victoria

Number of Pages Required

4 page

Colors
ec1f27
ffffff

Requirements
Must have
• This page must be clean, be in line with company branding and a high converting lead website.

```html
<!DOCTYPE html>
<html lang="en">
<head>
<meta charset="utf-8">
<title>Varno Electrical</title>
<link rel="stylesheet" href="https://fonts.googleapis.com/css2?family=Open+Sans:wght@300;400;600;700&display=swap">
<style>
:root{
  --red:#d42027;
  --red-bright:#ec1f27;
  --ink:#222;
  --text:#555;
  --muted:#999;
  --line:#ddd;
  --panel:#f3f3f3;
  --footer:#333;
  --white:#fff;
}
*{box-sizing:border-box;margin:0;padding:0}
html,body{width:750px;height:1200px;overflow:hidden;background:var(--white);font-family:"Open Sans",Arial,sans-serif;color:var(--text)}
.page{position:relative;width:750px;height:1200px}
.abs{position:absolute}

/* header */
.brand{left:83px;top:30px;display:flex;align-items:center;gap:8px}
.brand-mark{width:16px;height:16px;border-radius:50%;background:var(--red)}
.brand-name{font-size:26px;font-weight:700;color:var(--ink);letter-spacing:-.5px}
.brand-tag{left:95px;top:63px;font-size:9px;color:var(--ink)}
.phone{right:83px;top:26px;font-size:12.5px;color:var(--ink);display:flex;align-items:center;gap:4px}
.nav{right:83px;top:61px;display:flex;gap:18px;font-size:7px;text-transform:uppercase;letter-spacing:.2px}
.nav span{color:var(--muted)}
.nav .active{color:var(--ink)}
.nav .service{color:var(--red)}

/* hero */
.hero{left:0;top:96px;width:750px;height:288px;background:linear-gradient(180deg,#8c8c8c 0%,#a9a9a9 45%,#8a8a8a 100%)}
.hero-title{left:0;top:204px;width:750px;text-align:center;color:var(--white);font-weight:700;font-size:17px;line-height:22px;text-transform:uppercase;text-shadow:0 1px 2px rgba(0,0,0,.3)}
.hero-btn{left:347px;top:250px;width:56px;height:22px;background:var(--white);border-radius:2px;font-size:7px;color:var(--ink);display:flex;align-items:center;justify-content:center}
.slide-arrow{top:229px;width:16px;height:20px;background:rgba(0,0,0,.25);display:flex;align-items:center;justify-content:center}

/* service cards */
.card{top:354px;width:186px;height:150px}
.card-head{height:30px;background:var(--red);color:var(--white);font-size:14px;font-weight:600;text-transform:uppercase;display:flex;align-items:center;justify-content:center;gap:4px}
.card-img{height:120px}

/* about */
.about-title{left:0;top:548px;width:750px;text-align:center;color:var(--red);font-size:21px;font-weight:400}
.about-text{left:82px;top:579px;width:586px;text-align:center;font-size:7.8px;line-height:13px;color:var(--ink)}
.rule{left:82px;top:629px;width:586px;height:1px;background:var(--line)}
.ghost-btn{left:349px;top:617px;width:52px;height:24px;background:var(--white);border:1px solid var(--line);font-size:6.5px;color:var(--muted);display:flex;align-items:center;justify-content:center}

/* reasons */
.why-title{left:0;top:668px;width:750px;text-align:center;font-size:15px;color:var(--ink)}
.reason{top:702px;width:100px}
.reason svg{display:block;height:20px}
.reason h3{margin-top:6px;font-size:10px;font-weight:400;color:var(--red);line-height:13px}
.reason p{margin-top:7px;font-size:5.4px;line-height:10px;color:#777}

/* testimonial */
.quote-box{left:82px;top:882px;width:586px;height:108px;background:var(--panel)}
.quote-img{left:84px;top:882px;width:167px;height:108px;background:linear-gradient(180deg,#f7f7f7 0%,#f7f7f7 38%,#8f96a8 40%,#c9b8bc 75%,#5c5f66 100%)}
.quote-text{left:273px;top:893px;width:380px;font-size:13.5px;font-weight:300;line-height:20px;color:#555}
.quote-by{left:273px;top:961px;font-size:8px;color:var(--red)}
.q-arrow{top:926px}

/* clients */
.client{top:1000px;width:140px;height:80px;display:flex;align-items:center;justify-content:center;font-size:15px;font-weight:700}

/* footer */
.footer{left:0;top:1130px;width:750px;height:70px;background:var(--footer)}
.foot-links{left:82px;top:1150px;font-size:6.4px;color:#ccc;display:flex;gap:6px}
.copy{left:82px;top:1170px;font-size:6.4px;color:#ccc}
.foot-brand{left:524px;top:1154px;display:flex;align-items:center;gap:5px;color:var(--white);font-weight:700;font-size:17px}
.foot-brand i{width:11px;height:11px;border-radius:50%;background:var(--red);display:block}
.social{top:1157px;width:15px;height:15px;border-radius:50%}
.ver{left:732px;top:1183px;font-size:6px;color:#aaa}
</style>
</head>
<body>
<div class="page">

  <!-- header -->
  <div class="abs brand"><span class="brand-mark"></span><span class="brand-name">VARNO</span></div>
  <div class="abs brand-tag">Spark Every Day</div>
  <div class="abs phone">
    <svg width="6" height="10" viewBox="0 0 6 10"><rect x=".5" y=".5" width="5" height="9" rx="1" fill="none" stroke="#222"/></svg>
    13 7710 VARNO
  </div>
  <nav class="abs nav">
    <span class="active">Home</span><span>Varno Story</span><span>Our Work</span><span>Contact Us</span>
    <span class="service">Electrical</span><span class="service">LED Lighting</span><span class="service">Solar Power</span>
  </nav>

  <!-- hero -->
  <div class="abs hero" role="img" aria-label="Office ceiling with rows of LED panel lights"></div>
  <div class="abs slide-arrow" style="left:0"><svg width="6" height="10"><path d="M5 1 1 5l4 4" fill="none" stroke="#ddd"/></svg></div>
  <div class="abs slide-arrow" style="left:734px"><svg width="6" height="10"><path d="M1 1l4 4-4 4" fill="none" stroke="#ddd"/></svg></div>
  <h1 class="abs hero-title">Australia’s largest fully integrated<br>electrical &amp; energy solutions provider</h1>
  <div class="abs hero-btn">Read more</div>

  <!-- services -->
  <div class="abs card" style="left:82px">
    <div class="card-head"><svg width="7" height="12" viewBox="0 0 7 12"><path d="M4 0 0 7h3l-1 5 5-7H4z" fill="#fff"/></svg>Electrical</div>
    <div class="card-img" role="img" aria-label="Electrician working at a switchboard" style="background:linear-gradient(120deg,#9aa0a4,#c89a5c 60%,#8a6a40)"></div>
  </div>
  <div class="abs card" style="left:282px">
    <div class="card-head"><svg width="8" height="12" viewBox="0 0 8 12"><circle cx="4" cy="4" r="3.2" fill="none" stroke="#fff" stroke-width="1.2"/><rect x="2.5" y="8" width="3" height="3" fill="#fff"/></svg>LED Lighting</div>
    <div class="card-img" role="img" aria-label="Person holding an LED light bulb" style="background:linear-gradient(135deg,#e6e2de,#c9b3a6 50%,#f5f5f5)"></div>
  </div>
  <div class="abs card" style="left:482px">
    <div class="card-head"><svg width="12" height="12" viewBox="0 0 12 12"><circle cx="6" cy="6" r="3.5" fill="none" stroke="#fff" stroke-width="1.2"/><path d="M6 0v2M6 10v2M0 6h2M10 6h2" stroke="#fff" stroke-width="1.2"/></svg>Solar Power</div>
    <div class="card-img" role="img" aria-label="Installers fitting solar panels on a roof" style="background:linear-gradient(160deg,#9cc3e6,#2c54a8 50%,#1d3b7e 80%,#8b6e5c)"></div>
  </div>

  <!-- about -->
  <h2 class="abs about-title">About Us</h2>
  <p class="abs about-text">Varno Electrical was formed to be an expert Electricity Contracting Company providing services to all Residential and Commercial Customers. With over 10 years of experience, Varno Electrical has developed a highly-experienced team of professionals that ensure all our customer expectations are met.</p>
  <div class="abs rule"></div>
  <div class="abs ghost-btn">Read more</div>

  <!-- why choose us -->
  <h2 class="abs why-title">Why Choose Us?</h2>

  <div class="abs reason" style="left:83px">
    <svg width="20" height="20" viewBox="0 0 20 20"><path d="M2 18 11 9" stroke="#d42027" stroke-width="3" stroke-linecap="round"/><circle cx="14" cy="6" r="4.5" fill="#d42027"/><circle cx="16" cy="4" r="2" fill="#fff"/></svg>
    <h3>Professional service</h3>
    <p>When you hire a Varno Electrical Electrician you will get a professional and well-presented Electrician that comes skilled and ready to do the job.</p>
  </div>
  <div class="abs reason" style="left:205px">
    <svg width="20" height="20" viewBox="0 0 20 20"><rect x="1" y="3" width="18" height="16" rx="1" fill="none" stroke="#d42027" stroke-width="2"/><rect x="1" y="3" width="18" height="4" fill="#d42027"/><path d="M5 11h2M9 11h2M13 11h2M5 15h2M9 15h2M13 15h2" stroke="#d42027" stroke-width="2"/></svg>
    <h3>5 year workmanship guarantee</h3>
    <p>You can buy with confidence as all of our work has a 5 year workmanship guarantee. For your peace of mind, we unconditionally back our electrical work. We will come back to fix any problems at our own expense.</p>
  </div>
  <div class="abs reason" style="left:327px">
    <svg width="22" height="20" viewBox="0 0 22 20"><rect x="1" y="4" width="20" height="12" fill="none" stroke="#d42027" stroke-width="2"/><circle cx="11" cy="10" r="3.5" fill="#d42027"/></svg>
    <h3>Value for Money</h3>
    <p>We provide extremely competitive pricing, which means you get value for money on quality that is comparable to the best in the industry.</p>
  </div>
  <div class="abs reason" style="left:449px">
    <svg width="20" height="20" viewBox="0 0 20 20"><circle cx="10" cy="10" r="8.5" fill="#d42027"/><path d="M6 6c2 1 3 3 2 5s1 4 0 6M12 3c0 3 3 3 4 6" fill="none" stroke="#fff" stroke-width="1.5"/></svg>
    <h3>Environmentally friendly</h3>
    <p>We are committed to reducing carbon emissions by installing Solar Power and upgrading sites to LED Lighting. In addition to reducing the carbon emissions we recycle Fluorescent Tubes, High-bay Globes, Metal and Cardboard.</p>
  </div>
  <div class="abs reason" style="left:571px">
    <svg width="18" height="20" viewBox="0 0 18 20"><path d="M2 2h14v8c0 5-4 8-7 9-3-1-7-4-7-9z" fill="#d42027"/><path d="M9 5v11" stroke="#fff" stroke-width="3"/></svg>
    <h3>Fully insured</h3>
    <p>Varno Electrical is fully insured and equipped to handle break downs and service call outs.</p>
  </div>

  <!-- testimonial -->
  <div class="abs quote-box"></div>
  <div class="abs quote-img" role="img" aria-label="Client store interior with shop signage above"></div>
  <p class="abs quote-text">They clean up after the job, explained everything I needed to know and answered all questions, very professional. Will use them again in the future!</p>
  <div class="abs quote-by">- R. Delmar, Kew East VIC</div>
  <svg class="abs q-arrow" style="left:58px" width="8" height="14" viewBox="0 0 8 14"><path d="M7 1 1 7l6 6" fill="none" stroke="#aaa" stroke-width="1.3"/></svg>
  <svg class="abs q-arrow" style="left:683px" width="8" height="14" viewBox="0 0 8 14"><path d="M1 1l6 6-6 6" fill="none" stroke="#aaa" stroke-width="1.3"/></svg>

  <!-- clients -->
  <div class="abs client" style="left:82px;background:#f2f2f2;color:#d42027">Brightvale</div>
  <div class="abs client" style="left:231px;background:#f7ec15;color:#222">Outpost Gear</div>
  <div class="abs client" style="left:379px;background:#e8322a;color:#fff">Heron Plumbing</div>
  <div class="abs client" style="left:528px;background:#d41c1c;color:#f7c516">Golden Grill</div>

  <!-- footer -->
  <footer class="abs footer"></footer>
  <div class="abs foot-links"><span>Led Lighting</span>|<span>Solar Power</span>|<span>Electrical</span>|<span>Career</span>|<span>Terms and Conditions</span>|<span>Privacy</span></div>
  <div class="abs copy">Copyright © 2017 Company name. All rights reserved.</div>
  <div class="abs foot-brand"><i></i>VARNO</div>
  <div class="abs social" style="left:611px;background:#3b5a99"></div>
  <div class="abs social" style="left:632px;background:#c8302a"></div>
  <div class="abs social" style="left:653px;background:#4a8fbf"></div>
  <div class="abs ver">M2</div>
</div>
</body>
</html>
```